Moxy Fen needs some awesome stationary

Do you have what it takes to get my brand? You either do or you don't, have a crack at a design and you my just win my business.

I don't want to waste your or my time, so put your creative genius on either a business card or envelope.

I however need a package of stationary that follows the same brand. I will message you to complete the remaining should I like your first submission.

Here is what I need, have a go!

Basically I need the following for my small business based in melbourne.
- Letterhead (printer ready and MS Word)
- Business Card
- Compliments Slip
- Envelope
- Proposal Cover Page (MS Word only)
- Presentation Folder
- Marbled Fox Cards
- Student Name Tent
- Index Cards
- Vell-Ka

I am establishing the brand and it must be modern, professional but also relaxed; that is not formal and not corporate. It represents a company are leaders, but small enough to care and operate like a bunch of friends. We are bringing people and conversations back to business, and turfing out all the bureaucracy and crazy and wasteful procedures. Its about "lets talk and figure it out together and find even better ways".

Target Market(s)

Mainly companies that build software products, but Agile practices are used in many other industries (even graphic design projects)

Industry/Entity Type

Information Technology

Font styles to use
Sans Serif

Colors
3176b5
aaaaaa

Requirements
Must have
• I like curves and circles and not boxes or rectangles.
• I want a colour rich design with my brand colours, but it must be balanced.
• I want more modern than traditional, but simple modern
Should not have
• Not corporate
• Please don't waste my time if your not going to think about it.
• Don't mess with my primary logo
• Don't change my colours
• Don't overlay logo on image

```html
<!DOCTYPE html>
<html lang="en">
<head>
<meta charset="utf-8">
<title>Moxy Fen – Student Name Tents</title>
<link rel="stylesheet" href="https://fonts.googleapis.com/css2?family=Open+Sans:wght@600&family=Saira+Semi+Condensed:wght@400&display=swap">
<style>
  :root {
    --backdrop: #3a9fd8;
    --brand-blue: #2159a8;
    --band-blue: #1a7fd0;
    --band-grey: #b9b9b9;
    --paper: #ffffff;
    --rule: #9a9a9a;
    --frame: #8c8c8c;
  }
  * { margin: 0; padding: 0; box-sizing: border-box; }
  html, body { width: 1200px; height: 1200px; overflow: hidden; }
  body { background: var(--backdrop); position: relative; }

  .name-tent {
    position: absolute;
    left: 42px;
    width: 1116px;
    height: 464px;
    background: var(--paper);
    box-shadow: 4px 6px 8px rgba(0, 0, 0, 0.28);
  }
  .name-tent--solid { top: 82px; }
  .name-tent--outline { top: 618px; height: 466px; }

  .tent-band {
    position: absolute;
    left: 0;
    width: 100%;
    height: 13px;
    display: block;
  }
  .tent-band--top { top: 0; }
  .tent-band--bottom { bottom: 0; }

  .tent-fold {
    position: absolute;
    left: 0;
    right: 0;
    top: 232px;
    height: 1px;
    background: var(--rule);
  }

  .tent-face {
    position: absolute;
    left: 0;
    width: 100%;
    height: 232px;
    overflow: hidden;
  }
  .tent-face--back { top: 0; transform: rotate(180deg); }
  .tent-face--front { top: 232px; }

  /* Solid variant: brand block + name */
  .brand-block {
    position: absolute;
    left: 38px;
    top: 0;
    width: 229px;
    height: 220px;
    background: var(--brand-blue);
    display: flex;
    flex-direction: column;
    align-items: center;
    justify-content: center;
    gap: 22px;
    padding-top: 12px;
  }
  .brand-block__dot {
    width: 118px;
    height: 118px;
    border-radius: 50%;
    background: var(--paper);
  }
  .brand-name {
    font-family: "Open Sans", sans-serif;
    font-weight: 600;
    font-size: 35px;
    line-height: 1;
    white-space: nowrap;
  }
  .brand-block .brand-name { color: var(--paper); }

  .attendee-name {
    font-family: "Saira Semi Condensed", sans-serif;
    font-weight: 400;
    color: var(--brand-blue);
    line-height: 1;
    white-space: nowrap;
  }
  .name-tent--solid .attendee-name {
    position: absolute;
    left: 420px;
    width: 640px;
    top: 0;
    height: 220px;
    display: flex;
    align-items: center;
    justify-content: center;
    font-size: 170px;
    letter-spacing: 1px;
  }

  /* Outline variant: open mark + framed name */
  .brand-mark {
    position: absolute;
    left: 60px;
    top: 22px;
    width: 220px;
    display: flex;
    flex-direction: column;
    align-items: center;
    gap: 18px;
  }
  .brand-mark__dot {
    width: 126px;
    height: 126px;
    border-radius: 50%;
    background: var(--brand-blue);
  }
  .brand-mark .brand-name { color: var(--brand-blue); }

  .name-frame {
    position: absolute;
    left: 463px;
    top: 26px;
    width: 549px;
    height: 173px;
    border: 1px solid var(--frame);
    border-radius: 22px;
    display: flex;
    align-items: center;
    justify-content: center;
    overflow: hidden;
  }
  .name-frame .attendee-name { font-size: 148px; letter-spacing: 1px; }
</style>
</head>
<body>

  <section class="name-tent name-tent--solid">
    <svg class="tent-band tent-band--top" viewBox="0 0 1116 13" preserveAspectRatio="none" aria-hidden="true">
      <polygon points="0,0 808,0 796,13 0,13" fill="var(--band-blue)"/>
      <polygon points="818,0 1116,0 1116,13 806,13" fill="var(--band-grey)"/>
    </svg>

    <div class="tent-face tent-face--back">
      <div class="brand-block">
        <span class="brand-block__dot"></span>
        <span class="brand-name">Moxy Fen</span>
      </div>
      <div class="attendee-name">Dorian</div>
    </div>

    <div class="tent-fold"></div>

    <div class="tent-face tent-face--front">
      <div class="brand-block">
        <span class="brand-block__dot"></span>
        <span class="brand-name">Moxy Fen</span>
      </div>
      <div class="attendee-name">Dorian</div>
    </div>

    <svg class="tent-band tent-band--bottom" viewBox="0 0 1116 13" preserveAspectRatio="none" aria-hidden="true">
      <polygon points="0,0 312,0 300,13 0,13" fill="var(--band-grey)"/>
      <polygon points="322,0 1116,0 1116,13 310,13" fill="var(--band-blue)"/>
    </svg>
  </section>

  <section class="name-tent name-tent--outline">
    <svg class="tent-band tent-band--top" viewBox="0 0 1116 13" preserveAspectRatio="none" aria-hidden="true">
      <polygon points="0,0 890,0 878,13 0,13" fill="var(--band-blue)"/>
      <polygon points="900,0 1116,0 1116,13 888,13" fill="var(--band-grey)"/>
    </svg>

    <div class="tent-face tent-face--back">
      <div class="brand-mark">
        <span class="brand-mark__dot"></span>
        <span class="brand-name">Moxy Fen</span>
      </div>
      <div class="name-frame"><span class="attendee-name">Dorian</span></div>
    </div>

    <div class="tent-fold"></div>

    <div class="tent-face tent-face--front">
      <div class="brand-mark">
        <span class="brand-mark__dot"></span>
        <span class="brand-name">Moxy Fen</span>
      </div>
      <div class="name-frame"><span class="attendee-name">Dorian</span></div>
    </div>

    <svg class="tent-band tent-band--bottom" viewBox="0 0 1116 13" preserveAspectRatio="none" aria-hidden="true">
      <polygon points="0,0 226,0 214,13 0,13" fill="var(--band-grey)"/>
      <polygon points="236,0 1116,0 1116,13 224,13" fill="var(--band-blue)"/>
    </svg>
  </section>

</body>
</html>
```